Business cards and stationary design

We just completed the design of our new logo and we need to print new business cards and letterhead for our nonprofit. We are looking for a fresh new design that shows off our new logo. On letterhead, we must have a column on the right or left to include our Board of Directors (up to 45 names) (see attachment)

Industry/Entity Type

Non-Profit

Contact Information for Business Card

Standard business card with name, title, Company name, mailing address phone numbers, email address and website. Tagline on back "Bringing the homeless home"

Font styles to use
Sans Serif

Requirements
Must have
• include pertinent information above
• new logo
• fonts compatible with logo
• should use logo colors only
Nice to have
• tag lines

```html
<!DOCTYPE html>
<html lang="en">
<head>
<meta charset="utf-8">
<title>Homeward Relief Center – Business Card</title>
<link rel="stylesheet" href="https://fonts.googleapis.com/css2?family=Roboto:wght@400;500;700&display=swap">
<style>
  :root {
    --backdrop: #e9e6e1;
    --paper: #fbfbfb;
    --teal: #1590b0;
    --teal-deep: #0f7f9c;
    --red: #d42127;
    --white: #ffffff;
    --shadow: rgba(40, 30, 20, 0.22);
  }
  * { margin: 0; padding: 0; box-sizing: border-box; }
  html, body {
    width: 1200px; height: 911px; overflow: hidden;
    background: var(--backdrop);
    font-family: "Roboto", Arial, sans-serif;
  }
  .canvas { position: relative; width: 1200px; height: 911px; }
  .card {
    position: absolute; top: 140px;
    width: 360px; height: 630px;
    box-shadow: 0 14px 30px var(--shadow);
    overflow: hidden;
  }
  .card--front { left: 190px; background: var(--paper); }
  .card--back { left: 650px; background: var(--red); }

  .front-shapes { position: absolute; inset: 0; }

  .brand {
    position: absolute; top: 150px; left: 0; right: 0;
    display: flex; align-items: center; justify-content: center; gap: 12px;
  }
  .brand__mark { width: 16px; height: 16px; background: var(--red); }
  .brand__name {
    color: var(--teal); font-weight: 700; font-size: 22px;
    letter-spacing: 2px; text-transform: uppercase; line-height: 1.15;
    text-align: center;
  }

  .contact {
    position: absolute; left: 0; right: 0; top: 415px;
    text-align: center; color: var(--white);
  }
  .contact__name { font-size: 24px; font-weight: 700; letter-spacing: 0.5px; }
  .contact__title { font-size: 15px; font-weight: 500; letter-spacing: 1px; margin-top: 2px; }
  .contact__address { font-size: 14px; line-height: 1.35; margin-top: 14px; }
  .contact__org { font-weight: 500; }
  .contact__lines { font-size: 14px; line-height: 1.4; margin-top: 14px; }

  .back-url {
    position: absolute; left: 26px; top: 60px;
    writing-mode: vertical-rl;
    color: var(--white); font-size: 13px; letter-spacing: 5px;
  }
  .back-brand {
    position: absolute; top: 0; bottom: 0; left: 60px; right: 30px;
    display: flex; align-items: center; justify-content: center; gap: 12px;
  }
  .back-brand__mark { width: 16px; height: 16px; border-radius: 50%; background: var(--white); flex: none; }
  .back-brand__name {
    color: var(--white); font-weight: 700; font-size: 26px;
    letter-spacing: 2px; text-transform: uppercase; line-height: 1.2;
  }
</style>
</head>
<body>
<main class="canvas">
  <section class="card card--front" aria-label="Business card front">
    <svg class="front-shapes" width="360" height="630" viewBox="0 0 360 630" aria-hidden="true">
      <path d="M0,335 Q170,262 360,330 L360,630 L0,630 Z" fill="var(--red)"/>
      <path d="M0,352 Q170,282 360,348 L360,630 L0,630 Z" fill="var(--teal)"/>
      <path d="M0,352 Q170,282 360,348 L360,356 Q170,292 0,362 Z" fill="var(--teal-deep)" opacity="0.35"/>
    </svg>
    <div class="brand">
      <span class="brand__mark"></span>
      <span class="brand__name">Homeward Relief<br>Center</span>
    </div>
    <div class="contact">
      <p class="contact__name">DANA WHITFIELD</p>
      <p class="contact__title">CEO/FOUNDER</p>
      <p class="contact__address">
        <span class="contact__org">Homeward Relief Center</span><br>
        1420 Larkspur Avenue<br>
        Fairbanks, Alaska 99701
      </p>
      <p class="contact__lines">
        P. 555 214 7790<br>
        dana@homewardrelief.org<br>
        www.homewardrelief.org
      </p>
    </div>
  </section>

  <section class="card card--back" aria-label="Business card back">
    <p class="back-url">www.homewardrelief.org</p>
    <div class="back-brand">
      <span class="back-brand__mark"></span>
      <span class="back-brand__name">Homeward<br>Relief</span>
    </div>
  </section>
</main>
</body>
</html>
```